Easy Marinade Labels for Butchery Store

Need a set of labels designed for a Butchery Shop. They will sit in the top left corner of the packets as a triangle (7cm each side). Easy because the only major requirement is the label name and some small text saying "Please ask in store to see spec sheet for ingredients". Extra points for finding a fun way to incorporate the logo and/or images of food (garlic bulbs, chilli, spices ect) to enhance the label. List of Marinade Names below: GarlicPepper Mint & RosemarySatayBBQChilli Plum & GingerSundried Tomato & BasilBuffaloHoney SoyHoi-SinPer PeriSpicy CajunTeriyakiBlack Bean Ive also attached the logo and an example of how the label might sit on a packet of meat. Thanks

Target Market(s)

Butchery Deli Shop Customers

Industry/Entity Type

Food Store

Font styles to use
Serif
Sans Serif
Decorative
Other font styles liked:
• Fun font that isn't a generic Quellbrix Font?

Colors

Designer to choose colors to be used in the design.

Requirements
Must have
• Product Name
• Small text saying "Please ask in store to see spec sheet for ingredients"
Nice to have
• Photos of ingredients that would match that type of marinade - Chilli, Garlic, Spices.
• Fenly Oak Logo - not essential if it doesn't look good on the label / doesn't fit.

```html
<!DOCTYPE html>
<html lang="en">
<head>
<meta charset="utf-8">
<title>Fenly Oak – Cajun Marinade Label</title>
<link rel="stylesheet" href="https://fonts.googleapis.com/css2?family=Permanent+Marker&family=Josefin+Sans:wght@700&family=Fira+Sans+Condensed:wght@400&family=Playfair+Display:wght@700&display=swap">
<style>
  :root {
    --paper: #ffffff;
    --frame: #741011;
    --accent-red: #e33125;
    --note-red: #b8383a;
    --brand-red: #a81c1e;
    --spice-orange: #d9661f;
    --spice-gold: #e9a634;
    --spice-brown: #c98a4a;
    --herb-green: #3f8a3a;
    --herb-dark: #255f26;
  }
  html, body {
    margin: 0;
    padding: 0;
    width: 1200px;
    height: 900px;
    overflow: hidden;
    background: var(--paper);
  }
  .label-canvas {
    display: block;
    width: 1200px;
    height: 900px;
  }
  .brand-name {
    font-family: "Playfair Display", serif;
    font-weight: 700;
    font-size: 24px;
    fill: var(--brand-red);
  }
  .marinade-intro {
    font-family: "Josefin Sans", sans-serif;
    font-weight: 700;
    font-size: 15px;
    letter-spacing: 2px;
    fill: var(--accent-red);
  }
  .marinade-name {
    font-family: "Permanent Marker", cursive;
    font-size: 78px;
    letter-spacing: 2px;
    fill: var(--accent-red);
  }
  .ingredients-note {
    font-family: "Fira Sans Condensed", sans-serif;
    font-size: 21px;
    letter-spacing: 2.4px;
    fill: var(--note-red);
  }
</style>
</head>
<body>
<svg class="label-canvas" viewBox="0 0 1200 900" xmlns="http://www.w3.org/2000/svg">
  <defs>
    <clipPath id="label-inner">
      <polygon points="613,226 188,652 1038,652"/>
    </clipPath>
    <radialGradient id="spice-tones" cx="0.6" cy="0.45" r="0.6">
      <stop offset="0" stop-color="var(--spice-orange)"/>
      <stop offset="0.45" stop-color="var(--spice-gold)"/>
      <stop offset="0.8" stop-color="var(--spice-brown)" stop-opacity="0.6"/>
      <stop offset="1" stop-color="#ffffff" stop-opacity="0"/>
    </radialGradient>
    <radialGradient id="herb-tones" cx="0.45" cy="0.4" r="0.6">
      <stop offset="0" stop-color="var(--herb-dark)"/>
      <stop offset="0.55" stop-color="var(--herb-green)"/>
      <stop offset="1" stop-color="#ffffff" stop-opacity="0"/>
    </radialGradient>
  </defs>

  <g class="label">
    <polygon class="label-frame" points="613,205 150,667 1077,667" fill="var(--frame)"/>
    <polygon class="label-field" points="613,226 188,652 1038,652" fill="var(--paper)"/>

    <g class="label-imagery" clip-path="url(#label-inner)">
      <ellipse class="spice-piles" role="img" aria-label="Piles of ground cajun spices: paprika, turmeric and dried herbs"
               cx="430" cy="470" rx="175" ry="120" fill="url(#spice-tones)" transform="rotate(-32 430 470)"/>
      <ellipse class="herb-bunch" role="img" aria-label="Bunch of fresh basil, rosemary and thyme"
               cx="810" cy="460" rx="150" ry="125" fill="url(#herb-tones)" transform="rotate(30 810 460)"/>
    </g>

    <text class="brand-name" x="613" y="337" text-anchor="middle">Fenly Oak</text>

    <text class="marinade-intro" x="614" y="459" text-anchor="middle">MARINATED WITH</text>
    <text class="marinade-name" x="614" y="546" text-anchor="middle">CAJUN</text>

    <text class="ingredients-note" x="614" y="637" text-anchor="middle">PLEASE ASK IN STORE TO SEE SPEC SHEET FOR INGREDIENTS</text>
  </g>
</svg>
</body>
</html>
```